Webdesign für Steuerberaterin
Zielgruppe
Ich bin Steuerberaterin. Meine Zielgruppe sind sowohl Privatpersonen als auch Unternehmer sowie Männer und Frauen.
Aufgabenstellung
Bitte mein Logo und Foto mit berücksichtigen. Ich möchte keine Website, auf der alle 'Reiter' als eine Seite von oben nach unten durchlaufen. Sondern wirklich einzelne, voneinander getrennte Seiten.

```html
<!DOCTYPE html>
<html lang="de">
<head>
<meta charset="utf-8">
<title>Steuerberatung Maren Brodtke</title>
<link rel="stylesheet" href="https://fonts.googleapis.com/css2?family=Poppins:wght@600;700;800&family=Inter:wght@400;500;600&display=swap">
<style>
:root{
  --navy:#14213f;
  --page:#f3f6fb;
  --white:#ffffff;
  --ink:#0b0b0b;
  --footer-text:#b9c0cf;
  --gold:#c9a544;
  --tone-blue:#dbe9fb;
  --tone-green:#5dd36a;
  --tone-sky:#8cbcf2;
  --tone-steel:#3a6aa6;
}
*{margin:0;padding:0;box-sizing:border-box}
html,body{width:1200px;height:2404px;overflow:hidden}
body{background:var(--page);font-family:"Inter",sans-serif;color:var(--ink);position:relative}
.site-header{position:absolute;top:0;left:0;width:1200px;height:94px;background:var(--white);border-bottom:1px solid #e2e6ee}
.brand{position:absolute;left:112px;top:36px;display:flex;align-items:center;gap:8px;font-family:"Poppins",sans-serif;font-weight:600;font-size:15px;color:var(--navy)}
.brand-dot{width:12px;height:12px;border-radius:50%;background:var(--gold)}
.main-nav{position:absolute;top:0;left:403px;display:flex;height:94px}
.main-nav a{font-family:"Poppins",sans-serif;font-weight:600;font-size:13px;color:var(--navy);text-decoration:none;height:94px;line-height:92px;padding:0 23px;position:relative}
.main-nav a.active::after{content:"";position:absolute;left:0;right:0;top:63px;height:3px;background:var(--navy)}
.hero{position:absolute;top:94px;left:0;width:1200px;height:568px;background:linear-gradient(120deg,#4a5a78 0%,#6e7d98 40%,#3a4a6a 75%,#1f2d4c 100%)}
.hero-text{position:absolute;top:306px;left:0;width:1200px;text-align:center;color:var(--white)}
.hero-text h1{font-family:"Poppins",sans-serif;font-weight:700;font-size:50px;line-height:52px;letter-spacing:.5px}
.hero-text p{margin-top:14px;font-size:13px;font-weight:500;letter-spacing:.2px}
.intro-photo{position:absolute;left:30px;top:788px;width:540px;height:360px;background:linear-gradient(90deg,#d8d8d8,#f2f2f2 45%,#e2e2e2)}
.intro-text{position:absolute;left:608px;top:792px;width:545px}
.intro-text h2{font-family:"Poppins",sans-serif;font-weight:700;font-size:34px;line-height:42px;margin-bottom:14px}
.intro-text p{font-size:15px;line-height:22.5px;font-weight:500;margin-bottom:15px}
.services-title{position:absolute;top:1300px;left:0;width:1200px;text-align:center;font-family:"Poppins",sans-serif;font-weight:700;font-size:34px}
.services-rule{position:absolute;top:1360px;left:577px;width:46px;height:3px;background:var(--ink)}
.card{position:absolute;width:290px;height:194px;background:var(--white);text-align:center}
.card-icon{position:absolute;left:110px;top:20px;width:70px;height:70px;border-radius:6px}
.card h3{position:absolute;top:126px;left:0;width:100%;font-family:"Poppins",sans-serif;font-weight:700;font-size:17px;line-height:20px}
.site-footer{position:absolute;top:2141px;left:0;width:1200px;height:263px;background:var(--navy);color:var(--footer-text);font-size:16px}
.footer-col{position:absolute;top:42px}
.footer-col h4{color:var(--white);font-weight:500;font-size:15px;margin-bottom:20px}
.footer-col li{list-style:none;line-height:33px}
.footer-legal{left:400px;width:184px;text-align:center}
.footer-contact{left:668px}
</style>
</head>
<body>
<header class="site-header">
  <div class="brand"><span class="brand-dot"></span>Maren Brodtke</div>
  <nav class="main-nav">
    <a class="active" href="#">Startseite 1</a>
    <a href="#">Startseite 2</a>
    <a href="#">Leistungen</a>
    <a href="#">Leistungen 2</a>
    <a href="#">Über mich</a>
    <a href="#">Kontakt</a>
  </nav>
</header>

<section class="hero" role="img" aria-label="Foto: Hände an Laptop und Taschenrechner, blau getönt">
  <div class="hero-text">
    <h1>STEUERBERATUNG<br>MAREN BRODTKE</h1>
    <p>ICH FREUE MICH, DASS SIE DEN WEG ZU MIR GEFUNDEN HABEN!</p>
  </div>
</section>

<div class="intro-photo" role="img" aria-label="Porträtfoto der Steuerberaterin vor heller Steinwand"></div>
<div class="intro-text">
  <h2>Schön, dass Sie da sind!</h2>
  <p>Sie sind bei mir genau richtig: Egal, ob Sie Privatperson sind, die Ihre Einkommensteuer-Erklärung in vertrauensvolle Hände geben möchte, oder Unternehmer, der sich z.B. das „Rundum-Sorglos-Paket“ mit Buchführung, Jahresabschluss und Steuererklärungen wünscht.</p>
  <p>Schauen Sie sich hier gerne um und melden Sie sich bei mir – ich bin bei jedem steuerlichen Thema gerne Ihr kompetenter und zuverlässiger Ansprechpartner.</p>
  <p>Für mich ist es eine Selbstverständlichkeit, dass ich auch nach mehr als 12 Jahren Berufserfahrung durch permanente Fortbildungen immer auf dem aktuellsten Stand der relevanten Gesetze und Verordnungen bin. Nur so kann ich Sie bestmöglich beraten.</p>
</div>

<h2 class="services-title">Leistungen</h2>
<div class="services-rule"></div>

<div class="card" style="left:141px;top:1422px">
  <div class="card-icon" style="background:var(--tone-blue)" role="img" aria-label="Illustration: Steuerformular"></div>
  <h3>Einkommensteuer-<br>erklärung</h3>
</div>
<div class="card" style="left:455px;top:1422px">
  <div class="card-icon" style="background:var(--tone-blue)" role="img" aria-label="Illustration: Dokument mit Diagramm"></div>
  <h3>Betriebliche<br>Steuererklärungen</h3>
</div>
<div class="card" style="left:770px;top:1422px">
  <div class="card-icon" style="background:var(--tone-green)" role="img" aria-label="Illustration: Kassenbuch"></div>
  <h3>Finanzbuchführung</h3>
</div>

<div class="card" style="left:141px;top:1641px">
  <div class="card-icon" style="background:var(--tone-sky)" role="img" aria-label="Illustration: Kreisdiagramm"></div>
  <h3>Jahresabschluss (Bilanz)</h3>
</div>
<div class="card" style="left:455px;top:1641px">
  <div class="card-icon" style="background:var(--tone-steel)" role="img" aria-label="Illustration: Taschenrechner"></div>
  <h3>Einnahmen-überschuss-<br>rechnung</h3>
</div>
<div class="card" style="left:770px;top:1641px">
  <div class="card-icon" style="background:var(--tone-blue)" role="img" aria-label="Illustration: steigende Kurve"></div>
  <h3>Laufende steuerliche<br>Beratung</h3>
</div>

<div class="card" style="left:141px;top:1861px">
  <div class="card-icon" style="background:var(--tone-blue)" role="img" aria-label="Illustration: Lohnabrechnung mit Rechner"></div>
  <h3>Lohnbuchführung</h3>
</div>

<footer class="site-footer">
  <div class="footer-col footer-legal">
    <h4>Rechtliches</h4>
    <ul><li>Datenschutz</li><li>Impressum</li></ul>
  </div>
  <div class="footer-col footer-contact">
    <h4>Kontakt</h4>
    <ul><li>Maren Brodtke</li><li>Steuerberaterin</li><li>Lindenweg 14</li><li>24306 Seestadt</li></ul>
  </div>
</footer>
</body>
</html>
```